Bry7Legal Letterhead

Need a new letterhead for my law firm.
IDENTIFYING INFORMATION BELOW:
Anselmo R Quintara III
Attorney at Law
Address: 2847 Larkspur Blvd, Ste 300, Dallas, TX 75204
Phone: 877-482-6017
Fax: 469-738-1452
Email: bry@bry7legal.example
Website: www.bry7legal.example

Colors
0054AA
0677BA
7BADD7
CADEEF
E8F1F8

Requirements
Must have
• Logo needs to be on the letterhead, along with identifying information which is included in the project description.

```html
<!DOCTYPE html>
<html lang="en">
<head>
<meta charset="utf-8">
<title>Bry7Legal Letterhead</title>
<link rel="stylesheet" href="https://fonts.googleapis.com/css2?family=Lato:wght@400;700&family=Open+Sans:wght@400&display=swap">
<style>
  :root {
    --blue-deep: #0054AA;
    --blue: #0677BA;
    --blue-soft: #7BADD7;
    --blue-pale: #CADEEF;
    --blue-mist: #E8F1F8;
    --ink: #111111;
    --body: #4a4a4a;
    --rule: #c9c9c9;
    --backdrop: #e9eaec;
    --paper: #ffffff;
  }
  html, body {
    margin: 0;
    padding: 0;
    width: 1040px;
    height: 1200px;
    overflow: hidden;
    background: var(--backdrop);
  }
  .letterhead {
    position: absolute;
    left: 53px;
    top: 0;
    width: 934px;
    height: 1200px;
    background: var(--paper);
    font-family: "Open Sans", Arial, sans-serif;
    color: var(--body);
  }
  .side-band {
    position: absolute;
    left: 0;
    top: 0;
    width: 20px;
    height: 1200px;
  }
  .brand {
    position: absolute;
    left: 80px;
    top: 48px;
    display: flex;
    align-items: center;
    gap: 10px;
  }
  .brand-square {
    width: 14px;
    height: 14px;
    background: var(--blue-deep);
  }
  .brand-name {
    margin: 0;
    font-family: "Lato", Arial, sans-serif;
    font-weight: 400;
    font-size: 26px;
    line-height: 30px;
    color: var(--blue-deep);
  }
  .attorney {
    position: absolute;
    right: 97px;
    top: 48px;
    text-align: right;
    font-family: "Lato", Arial, sans-serif;
  }
  .attorney-name {
    display: block;
    font-weight: 700;
    font-size: 20px;
    line-height: 24px;
    color: var(--blue-deep);
  }
  .attorney-title {
    display: block;
    font-size: 17px;
    line-height: 22px;
    color: var(--ink);
  }
  .letter {
    position: absolute;
    left: 89px;
    right: 91px;
    top: 0;
    font-size: 14.5px;
    line-height: 27px;
  }
  .letter p { margin: 0; position: absolute; left: 0; right: 0; }
  .issue-date { top: 219px; }
  .recipient { top: 257px; line-height: 18px; }
  .salutation { top: 360px; }
  .body-copy { text-align: justify; }
  .para-1 { top: 414px; }
  .para-2 { top: 576px; }
  .para-3 { top: 684px; }
  .closing { top: 817px; }
  .signature-mark {
    position: absolute;
    left: 89px;
    top: 860px;
    width: 215px;
    height: 26px;
    background: var(--blue-mist);
    border-radius: 3px;
  }
  .signer {
    position: absolute;
    left: 89px;
    top: 898px;
  }
  .signer-name {
    display: block;
    font-size: 18.5px;
    line-height: 26px;
    color: #2b2b2b;
  }
  .signer-role {
    display: block;
    font-size: 15px;
    line-height: 24px;
    color: var(--body);
  }
  .contact {
    position: absolute;
    left: 90px;
    width: 754px;
    top: 1114px;
    text-align: center;
    font-family: "Lato", Arial, sans-serif;
    color: var(--ink);
    font-size: 16px;
  }
  .contact-address {
    margin: 0 59px;
    line-height: 26px;
    padding-bottom: 4px;
    border-bottom: 1.5px solid var(--rule);
    font-size: 17px;
  }
  .contact-lines {
    line-height: 26px;
    padding-top: 5px;
    white-space: nowrap;
  }
  .contact-label {
    color: var(--blue-deep);
    font-weight: 700;
  }
</style>
</head>
<body>
  <main class="letterhead">
    <svg class="side-band" viewBox="0 0 20 1200" aria-hidden="true">
      <defs>
        <linearGradient id="bandBlue" x1="0" y1="0" x2="0" y2="1">
          <stop offset="0" stop-color="#0677BA"/>
          <stop offset="1" stop-color="#0054AA"/>
        </linearGradient>
      </defs>
      <polygon points="0,0 20,0 20,560 0,535" fill="url(#bandBlue)"/>
      <polygon points="0,552 20,584 20,1200 0,1200" fill="#000000"/>
    </svg>

    <div class="brand">
      <span class="brand-square" aria-hidden="true"></span>
      <h1 class="brand-name">Bry7Legal</h1>
    </div>

    <div class="attorney">
      <span class="attorney-name">Anselmo R Quintara III</span>
      <span class="attorney-title">Attorney at Law</span>
    </div>

    <section class="letter">
      <p class="issue-date">Issuing Date: May 5, 2018</p>
      <p class="recipient">Name Of Employee Mr. XYZABC<br>Address of Employee<br>Address Line 2 etc..</p>
      <p class="salutation">Dear Mr.XYZABC</p>
      <p class="body-copy para-1">Lorem Ipsum has been the industry's standard dummy text ever since the 1500s, when an unknown printer took a galley of type and scrambled it to make a type specimen book. It has survived not only five centuries, but also the leap into electronic typesetting, remaining essentially unchanged. It was popularised in the 1960s with the release of Transfertype sheets containing Lorem Ipsum passages, and more recently with desktop publishing software like Quillset Layout including versions of Lorem Ipsum.</p>
      <p class="body-copy para-2">Lorem Ipsum is simply dummy text of the printing and typesetting industry. Lorem Ipsum has been the industry's standard dummy text ever since the 1500s, when an unknown printer took a galley of type and scrambled it to make a type specimen book.</p>
      <p class="body-copy para-3">It has survived not only five centuries, but also the leap into electronic typesetting, remaining essentially unchanged. It was popularised in the 1960s with the release of Transfertype sheets containing Lorem IpsumIpsum passages.</p>
      <p class="closing">Yours Sincerely</p>
    </section>

    <div class="signature-mark" role="img" aria-label="Handwritten signature of Desmond Harlow"></div>

    <div class="signer">
      <span class="signer-name">Desmond Harlow</span>
      <span class="signer-role">Managing Director</span>
    </div>

    <footer class="contact">
      <div class="contact-address">2847 Larkspur Blvd, Ste 300, Dallas, TX 75204</div>
      <div class="contact-lines">
        <span class="contact-label">P:</span> 877-482-6017 &nbsp;|&nbsp; <span class="contact-label">F:</span> 469-738-1452 | <span class="contact-label">E:</span> bry@bry7legal.example &nbsp;|&nbsp; <span class="contact-label">W:</span> www.bry7legal.example
      </div>
    </footer>
  </main>
</body>
</html>
```